Brightfield Ventures Inc. Letterhead

Creation of attractive and eye catching letterhead for a business start-up for the construction industry. Letterhead must relate to construction, but avoid standard hammer and tools in the design.

I forgot to add some details, sorry about that. Some pertinent info: Ph: 916-555-0187 brightfieldventures.example 448 Willowmere Ave, Ste 210 Folsom, CA 95999 info@brightfieldventures.example not sure if slogan should be in there" “Connecting construction professionals to create a purpose driven industry.” must be able to be used in word. Thanks!

```html
<!DOCTYPE html>
<html lang="en">
<head>
<meta charset="utf-8">
<title>Brightfield Ventures Inc. Letterhead</title>
<link rel="stylesheet" href="https://fonts.googleapis.com/css2?family=Open+Sans:wght@400;600;700&display=swap">
<style>
  :root {
    --navy: #101a3f;
    --red: #d3262c;
    --ink: #2b2b2b;
    --muted: #555a66;
    --paper: #ffffff;
    --backdrop: #8a847c;
  }
  * { box-sizing: border-box; margin: 0; padding: 0; }
  html, body { width: 1200px; height: 795px; overflow: hidden; }
  body {
    background: var(--backdrop);
    font-family: "Open Sans", Arial, sans-serif;
    color: var(--ink);
    display: flex; align-items: center; justify-content: center;
  }
  .letterhead {
    position: relative;
    width: 530px; height: 750px;
    background: var(--paper);
    overflow: hidden;
  }
  .brand {
    position: absolute; left: 52px; top: 52px;
    display: flex; align-items: center; gap: 9px;
  }
  .brand-mark { width: 16px; height: 16px; background: var(--red); }
  .brand-name {
    font-weight: 700; font-size: 15px; line-height: 1.05;
    letter-spacing: 0.06em; color: var(--navy); text-transform: uppercase;
  }
  .letter {
    position: absolute; left: 52px; top: 210px; width: 420px;
    font-size: 8.4px; line-height: 1.42;
  }
  .date { margin-bottom: 12px; }
  .recipient { margin-bottom: 14px; }
  .salutation { font-weight: 700; margin-bottom: 12px; }
  .letter p.body { color: var(--muted); margin-bottom: 11px; }
  .signoff {
    position: absolute; right: 48px; top: 265px;
    font-size: 8.4px; text-align: left;
  }
  .signature {
    display: block; width: 56px; height: 18px; margin-top: 8px;
    background: linear-gradient(90deg, #e9e9ec, #cfd1d8);
    border-radius: 2px;
  }
  .footer-wave { position: absolute; left: 0; top: 0; width: 530px; height: 750px; }
  .contact {
    position: absolute; left: 30px; bottom: 40px;
    display: flex; align-items: flex-end; gap: 14px;
    font-size: 7.6px; line-height: 1.45; color: var(--ink);
  }
  .contact-lines { list-style: none; }
  .contact-lines li { display: flex; align-items: center; gap: 4px; }
  .contact-icon {
    width: 7px; height: 7px; border-radius: 50%; background: var(--red);
    flex: none;
  }
</style>
</head>
<body>
  <main class="letterhead">
    <header class="brand">
      <span class="brand-mark"></span>
      <span class="brand-name">Brightfield<br>Ventures</span>
    </header>

    <section class="letter">
      <p class="date">January 12, 2014</p>
      <p class="recipient">Mr. John Doe<br>President<br>AA Corporation<br>111 Street Name, Suite#<br>City, State, 12345</p>
      <p class="salutation">Dear Mr. John,</p>
      <p class="body">Lorem Ipsum is simply dummy text of the printing and typesetting industry. Lorem Ipsum has been the industry's standard dummy text ever since the 1500s, when an unknown printer took a galley of type and scrambled it to make a type specimen book. It has survived not only five centuries, but also the leap into electronic typesetting, remaining essentially unchanged.</p>
      <p class="body">The standard chunk of Lorem Ipsum used since the 1500s is reproduced below for those interested. Sections 1.10.32 and 1.10.33 from "de Finibus Bonorum et Malorum" by Orvinus are also reproduced in their exact original form, accompanied by English versions from the 1914 translation by H. Marlowe.</p>
      <p class="body">Lorem Ipsum is simply dummy text of the printing and typesetting industry. Lorem Ipsum has been the industry's standard dummy text ever since the 1500s, when an unknown printer took a galley of type and scrambled it to make a type specimen book. It has survived not only five centuries, but also the leap into electronic typesetting, remaining essentially unchanged. It was popularised in the</p>
    </section>

    <div class="signoff">
      Sincerely Yours,
      <span class="signature" role="img" aria-label="Handwritten signature"></span>
    </div>

    <svg class="footer-wave" viewBox="0 0 530 750" aria-hidden="true">
      <defs>
        <linearGradient id="edgeGradient" x1="0" y1="1" x2="1" y2="0.5">
          <stop offset="0" stop-color="#d3262c"/>
          <stop offset="0.5" stop-color="#7a1f35"/>
          <stop offset="0.85" stop-color="#101a3f"/>
        </linearGradient>
      </defs>
      <path d="M0,750 C260,748 400,720 460,600 C500,520 515,420 530,330 L530,750 Z" fill="url(#edgeGradient)"/>
      <path d="M70,750 C300,746 430,724 482,615 C512,540 522,440 530,385 L530,750 Z" fill="var(--navy)"/>
    </svg>

    <footer class="contact">
      <p>448 Willowmere Ave, Ste 210,<br>Folsom, CA 95999</p>
      <ul class="contact-lines">
        <li><span class="contact-icon"></span>916-555-0187</li>
        <li><span class="contact-icon"></span>info@brightfieldventures.example</li>
        <li><span class="contact-icon"></span>www.brightfieldventures.example</li>
      </ul>
    </footer>
  </main>
</body>
</html>
```